Business Card Design Can you design a business card design? Looking for something unique and differe

Can you design a business card design? Looking for something unique and different. Can you design a business card design? Looking for something unique and different.Can you design a business card design? Looking for something unique and different.Can you design a business card design? Looking for something unique and different.Can you design a business card design? Looking for something unique and different.Can you design a business card design? Looking for something unique and different.

Industry/Entity Type

Business

Contact Information for Business Card

Can you design a business card design? Looking for something unique and different.

Font styles to use
Serif

```html
<!DOCTYPE html>
<html lang="en">
<head>
<meta charset="utf-8">
<title>Dosewell business card</title>
<link rel="stylesheet" href="https://fonts.googleapis.com/css2?family=Open+Sans:ital,wght@0,400;0,600;1,400&display=swap">
<style>
  :root {
    --bg: #d9d9d9;
    --card: #ffffff;
    --purple: #8a6d9f;
    --grey: #7b7b7b;
    --band-edge: #8f8f8f;
    --ink: #2b2b2b;
  }
  * { box-sizing: border-box; margin: 0; padding: 0; }
  html, body { width: 1200px; height: 852px; overflow: hidden; }
  body {
    background: var(--bg);
    font-family: "Open Sans", Arial, sans-serif;
    position: relative;
  }
  .card {
    position: absolute;
    width: 500px;
    height: 286px;
    background: var(--card);
    border-radius: 12px;
    overflow: hidden;
    box-shadow: 0 4px 10px rgba(0,0,0,.18);
  }
  .card--front { left: 90px; top: 110px; }
  .card--back { left: 610px; top: 456px; }

  .wordmark {
    display: flex; align-items: center; gap: 12px;
    color: var(--purple); font-weight: 600; letter-spacing: .5px;
    line-height: 1;
  }
  .wordmark__square { background: var(--purple); flex: none; }

  .card--front .wordmark {
    position: absolute; left: 0; right: 0; top: 118px;
    justify-content: center; font-size: 44px;
  }
  .card--front .wordmark__square { width: 30px; height: 30px; }

  .card--back .band {
    position: absolute; left: 0; top: 0; bottom: 0; width: 40px;
    background: var(--purple);
    border-right: 6px solid var(--band-edge);
  }
  .card--back .wordmark {
    position: absolute; left: 70px; top: 34px; font-size: 34px;
  }
  .card--back .wordmark__square { width: 24px; height: 24px; }

  .person { position: absolute; left: 70px; top: 128px; }
  .person__name { color: var(--purple); font-size: 17px; font-weight: 600; }
  .person__role { color: var(--ink); font-size: 10px; font-style: italic; margin-top: 1px; }

  .contact { position: absolute; left: 70px; top: 180px; list-style: none; }
  .contact__item {
    display: flex; align-items: center; gap: 9px;
    font-size: 11.5px; color: var(--ink); line-height: 20px;
  }
  .contact__icon { width: 11px; height: 11px; fill: var(--grey); flex: none; }
  .contact__icon--line { fill: none; stroke: var(--grey); stroke-width: 1.1; }
</style>
</head>
<body>
  <section class="card card--front" aria-label="Card front">
    <div class="wordmark"><span class="wordmark__square"></span>Dosewell</div>
  </section>

  <section class="card card--back" aria-label="Card back">
    <div class="band"></div>
    <div class="wordmark"><span class="wordmark__square"></span>Dosewell</div>
    <div class="person">
      <div class="person__name">Your Long Name</div>
      <div class="person__role">Managing Director</div>
    </div>
    <ul class="contact">
      <li class="contact__item">
        <svg class="contact__icon" viewBox="0 0 12 12"><path d="M2 1h2.5l1 3-1.5 1a6 6 0 0 0 3 3l1-1.5 3 1V11c-5 .5-9.5-4-9-10z"/></svg>
        00.00.00.0000
      </li>
      <li class="contact__item">
        <svg class="contact__icon contact__icon--line" viewBox="0 0 12 12"><path d="M.5 2h11v8H.5z M1 3l5 4 5-4"/></svg>
        yourname@yourwebsite.com
      </li>
      <li class="contact__item">
        <svg class="contact__icon contact__icon--line" viewBox="0 0 12 12"><circle cx="6" cy="6" r="5"/><ellipse cx="6" cy="6" rx="2.2" ry="5"/><path d="M1 6h10"/></svg>
        www.yourwebsite.com
      </li>
      <li class="contact__item">
        <svg class="contact__icon" viewBox="0 0 12 12"><path d="M6 0a4 4 0 0 1 4 4c0 3-4 8-4 8S2 7 2 4a4 4 0 0 1 4-4zm0 2.5a1.5 1.5 0 1 0 0 3 1.5 1.5 0 0 0 0-3z"/></svg>
        Your Commercial or office address with pincode
      </li>
    </ul>
  </section>
</body>
</html>
```